Birchwell Agency Condominium mail merge

We need a marketing proposal letter design to do a mail merge to potential e customers. We included our logo and an example of my miserable attempt to create a template. We are looking for a modern and attractive proposal template. Here is our website https://www.birchwellagency.example to be used for any additional information needed about us and our services.

Target Market(s)

New prospects

Industry/Entity Type

Insurance Agency

Requirements
Must have
• My project must have a modern professional look with merge fields similar to the file uploaded with this project.
Nice to have
• it would like have a condominium and a car icon graphic depicting there is additional discounts for both quotes bundled.
Should not have
• My project should not have any other logos or company name

```html
<!DOCTYPE html>
<html lang="en">
<head>
<meta charset="utf-8">
<title>Birchwell Agency – Condominium Proposal Letter</title>
<link href="https://fonts.googleapis.com/css2?family=Poppins:wght@500;600;700;800&family=Hind:wght@400;600&family=Merriweather:wght@400;700&family=Tinos&family=Great+Vibes&display=swap" rel="stylesheet">
<style>
  :root{
    --orange:#f47f21;
    --green:#3bb54a;
    --green-dark:#1f8a30;
    --sky:#29a8f0;
    --navy:#1e2a78;
    --red:#c8102e;
    --ink:#2b2b2b;
    --muted:#6f6f6f;
    --row-alt:#e9e9e9;
    --yellow:#ffe600;
  }
  *{box-sizing:border-box;margin:0;padding:0}
  html,body{width:848px;height:1200px;overflow:hidden;background:#fff}
  .letter{position:relative;width:848px;height:1200px;overflow:hidden;font-family:"Hind",sans-serif;color:var(--ink)}

  .brand{position:absolute;left:36px;top:40px;display:flex;align-items:center;gap:8px}
  .brand-dot{width:14px;height:14px;border-radius:50%;background:var(--orange)}
  .brand-name{font-family:"Poppins",sans-serif;font-weight:700;font-size:26px;color:var(--orange);letter-spacing:.2px}

  .recipient{position:absolute;left:38px;top:124px;font-family:"Tinos",serif;color:var(--ink)}
  .recipient .imb{font-size:16px;line-height:26px}
  .recipient p{font-size:12.5px;line-height:22.7px}
  .recipient .tray{font-size:14px}

  .bundle-badge{position:absolute;left:594px;top:13px;width:242px;height:195px;border:2px solid var(--navy);border-radius:30px;overflow:hidden;background:var(--green)}
  .bundle-scene{position:absolute;left:0;top:0;width:100%;height:140px;background:linear-gradient(160deg,var(--sky) 0%,#3fb2f2 45%,#a89a86 70%,#6a8f3c 100%);border-bottom-left-radius:60% 22px;border-bottom-right-radius:60% 22px}
  .bundle-title{position:absolute;left:7px;top:24px;display:flex;align-items:center;gap:6px;color:#fff}
  .bundle-title svg{width:27px;height:27px}
  .bundle-title .line1{font-family:"Poppins",sans-serif;font-weight:600;font-size:11px;line-height:11px}
  .bundle-title .line2{font-family:"Poppins",sans-serif;font-weight:800;font-style:italic;font-size:24px;line-height:24px}
  .bundle-copy{position:absolute;left:6px;right:6px;top:148px;text-align:center;font-family:"Poppins",sans-serif;font-size:7.6px;line-height:9.2px;color:#fff}
  .bundle-copy b{font-weight:700;font-size:8.6px}
  .bundle-copy .hl{color:var(--yellow);font-weight:700;font-size:8.6px}

  .proposal{position:absolute;right:24px;top:228px;text-align:right}
  .proposal h1{font-family:"Poppins",sans-serif;font-weight:700;font-size:17px;color:var(--green);letter-spacing:.3px}
  .proposal .date{font-family:"Tinos",serif;font-size:12px;color:var(--ink);margin-top:2px}

  .intro{position:absolute;left:38px;top:333px;width:779px}
  .intro .salute{font-weight:600;font-size:13.5px;line-height:21px}
  .intro p{font-size:13.5px;line-height:21.5px;text-align:justify}

  .coverage{position:absolute;left:35px;top:453px;width:778px;height:268px;border:1px solid #cfcfcf}
  .coverage-head{height:36px;background:var(--orange);display:flex;align-items:center;color:#fff;font-family:"Poppins",sans-serif;font-weight:500;font-size:13.5px}
  .coverage-head span:first-child{margin-left:27px;width:272px}
  .coverage-rows{width:492px}
  .coverage-row{display:flex;align-items:center;height:28.5px;font-size:12px;color:var(--muted)}
  .coverage-row:nth-child(even){background:var(--row-alt)}
  .coverage-row .label{margin-left:22px;width:278px}
  .coverage-row.strong .label{font-weight:600;color:#1a1a1a}
  .coverage-row.strong .value{font-weight:600}
  .premium{position:absolute;left:492px;top:36px;right:0;bottom:2px;background:var(--green);display:flex;flex-direction:column;align-items:center;justify-content:center;color:#fff;font-family:"Merriweather",serif;font-weight:700;text-align:center}
  .premium .cap{font-size:12.5px}
  .premium .amount{font-size:19px;margin-top:2px}

  .disclaimer{position:absolute;left:47px;top:725px;width:760px;color:var(--red);font-size:12px;line-height:21.5px}
  .closing-text{position:absolute;left:38px;top:780px;width:779px;font-size:13.5px;line-height:21.5px}

  .signoff{position:absolute;left:34px;top:916px}
  .signoff .regards{font-size:13.5px}
  .signoff .signature{font-family:"Great Vibes",cursive;font-size:30px;color:var(--navy);margin-top:8px;line-height:34px}
  .signoff .rule{width:165px;height:1px;background:#bdbdbd;margin-top:4px}
  .signoff .role{font-family:"Poppins",sans-serif;font-weight:500;font-size:12px;letter-spacing:1.8px;margin-top:6px}

  .footer{position:absolute;left:0;bottom:0;width:848px;height:120px}
  .footer svg{position:absolute;left:0;top:0}
  .footer-info{position:absolute;right:12px;top:50px;text-align:right;font-family:"Merriweather",serif;font-size:12.5px;line-height:21px;color:#fff}
  .footer-info b{font-weight:700}
</style>
</head>
<body>
<main class="letter">
  <div class="brand"><span class="brand-dot"></span><span class="brand-name">Birchwell Agency</span></div>

  <address class="recipient" style="font-style:normal">
    <div class="imb">«encodedimbno»</div>
    <p>«first_name1» «last_name1»</p>
    <p>&lt;&lt;Address&gt;&gt;</p>
    <p>&lt;&lt;Address2&gt;&gt;</p>
    <p>&lt;&lt;City&gt;&gt;, &lt;&lt;State&gt;&gt;, &lt;&lt;Zip&gt;&gt;</p>
    <div class="tray">«presorttrayid»</div>
  </address>

  <aside class="bundle-badge">
    <div class="bundle-scene" role="img" aria-label="Photo of a red sports car in front of a two-storey house"></div>
    <div class="bundle-title">
      <svg viewBox="0 0 28 28"><circle cx="14" cy="14" r="11.5" fill="none" stroke="#fff" stroke-width="2.5"/><path d="M14 8v12M8 14h12" stroke="#fff" stroke-width="3"/></svg>
      <div><div class="line1">COMBINE &amp;</div><div class="line2">$AVE</div></div>
    </div>
    <p class="bundle-copy">Switch your <b>Condominium</b> and <b>Auto Insurance</b> policy by visiting <span class="hl">Birchwellagency.example</span> today or calling <span class="hl">555.201.7740</span> to take advantage of additional discounts.</p>
  </aside>

  <div class="proposal">
    <h1>PROPOSAL NO</h1>
    <div class="date">Date: &lt;&lt;DATE&gt;&gt;</div>
  </div>

  <section class="intro">
    <div class="salute">Respected Sir,</div>
    <p>We have saved our clients $100s on their Condo Insurance. Call us at 555-201-7740 so we can do the same for you! Bundle your Condo and Auto insurance together for additional savings with a multi-policy discount. Below is a sample Condo Insurance policy purchased recently in Orlando from Birchwell Insurance Agency.</p>
  </section>

  <section class="coverage">
    <div class="coverage-head"><span>COVERAGE</span><span>LIMIT</span></div>
    <div class="coverage-rows">
      <div class="coverage-row"><span class="label">Personal Property Protection</span><span class="value">&lt;ColumnQ&gt;</span></div>
      <div class="coverage-row"><span class="label">Increased Additional Living Expense</span><span class="value">20%</span></div>
      <div class="coverage-row"><span class="label">Loss Assessments</span><span class="value">$2,000</span></div>
      <div class="coverage-row"><span class="label">Family Liability Protection</span><span class="value">$100,000</span></div>
      <div class="coverage-row"><span class="label">Building Property Protection</span><span class="value">&lt;ColumnK&gt;</span></div>
      <div class="coverage-row"><span class="label">Building Codes Coverages</span><span class="value">25%</span></div>
      <div class="coverage-row strong"><span class="label">All Perils Deductible</span><span class="value">$500</span></div>
      <div class="coverage-row strong"><span class="label">Hurricane&nbsp; Deductible</span><span class="value">$500</span></div>
    </div>
    <div class="premium">
      <div class="cap">Total Annual Premium:</div>
      <div class="amount">&lt;&lt;Yearly Premium&gt;&gt;</div>
    </div>
  </section>

  <p class="disclaimer">***The quoted premium is a sample premium based on a recent policy purchased in Orlando. Premium will differ based on information obtained on your application***</p>

  <p class="closing-text">If you are tired of paying too much for Condo Insurance and are wanting all of your insurance needs handled under one agency, then call us at 555-201.7740. One call is all it takes to see if you’ve got the right coverage at the right price.</p>

  <div class="signoff">
    <div class="regards">Sincerely,</div>
    <div class="signature">Nolan Birchwell</div>
    <div class="rule"></div>
    <div class="role">[ AGENCY PRINCIPAL ]</div>
  </div>

  <footer class="footer">
    <svg width="848" height="120" viewBox="0 0 848 120">
      <rect x="0" y="42" width="848" height="78" fill="var(--orange)"/>
      <polygon points="66,1 202,42 147,42" fill="var(--green-dark)"/>
      <polygon points="0,47 66,1 296,120 0,120" fill="var(--green)"/>
    </svg>
    <div class="footer-info">
      <div><b>A:</b> 742 Harrow Lane Ste. 210 Maplefield, FL 32000</div>
      <div><b>Phone:</b> 02 5550 1234 90 <b>Email:</b> info@BirchwellAgency.example, <b>Website:</b> BirchwellAgency.example</div>
    </div>
  </footer>
</main>
</body>
</html>
```